pet resort day care for our buisiness

we need a new web design for our pet center in Florida , we are provide the following services -
1. dog day car
2.dog/cat boarding
3. dog grooming
4. Dog training
5.pet food toy and clothing
our current websit is -http://www.tindlewoodpetcenter.com/
we are looking for a fresh new design that will reflect the change that we have made in the vusness from renovationnto the facelaty new management and new servises
Target Market(s)
Dog Lover , Upmarket
Industry/Entity Type
Pet
Number of Pages Required
5+ page
Font styles to use
Sans Serif
Requirements
Must have
- clean design , easy to understand and navigate , our target is the upmarket costumer how are dog lover
Should not have
- NOOO of the shelf design , confusing design , brown colors

```html
<!DOCTYPE html>
<html lang="en">
<head>
<meta charset="utf-8">
<title>Tindlewood Pet Center</title>
<link href="https://fonts.googleapis.com/css2?family=Cookie&family=Satisfy&family=Raleway:wght@400;600;700&display=block" rel="stylesheet">
<style>
:root{
  --pink:#ee4a6a;
  --pink-text:#e0395f;
  --dark:#1d1d1d;
  --darker:#111;
  --slate:#4f5a68;
  --ink:#222;
  --grey:#777;
  --line:#e6e6e6;
  --card:#f5f5f5;
  --lime:#b9cf4a;
  --script:"Satisfy","Cookie","Segoe Script","Brush Script MT",cursive;
  --sans:"Raleway","Helvetica Neue",Arial,sans-serif;
}
*{margin:0;padding:0;box-sizing:border-box}
html,body{width:705px;height:1200px;overflow:hidden;background:#fff}
body{font-family:var(--sans);color:var(--ink);position:relative}
.script{font-family:var(--script);font-weight:400;font-synthesis:none}
.abs{position:absolute}

.contact{top:44px;display:flex;align-items:center;gap:10px}
.contact .ring{width:20px;height:20px;border:2px solid var(--pink);border-radius:50%;display:flex;align-items:center;justify-content:center;flex:none}
.contact .label{font-family:var(--script);font-size:11px;display:block;line-height:13px}
.contact .value{font-family:var(--script);font-size:9.5px;line-height:12px}
.brand{left:300px;top:24px;width:105px;text-align:center}
.brand .mark{width:14px;height:14px;border-radius:50%;background:var(--slate);margin:0 auto 8px}
.brand .name{font-size:17px;font-weight:700;color:var(--lime);line-height:1}
.brand .sub{font-size:9px;font-weight:700;color:var(--pink);margin-top:3px}

.nav{top:108px;left:0;width:705px;height:26px;border-top:1px solid #333;border-bottom:1px solid var(--line);display:flex;padding-left:88px;font-size:7px;font-weight:600}
.nav a{text-decoration:none;color:#333;padding:0 16px;line-height:25px}
.nav a.active{color:var(--pink);border-top:2px solid var(--pink);line-height:22px}

.hero{top:134px;left:0;width:705px;height:288px;background:linear-gradient(180deg,#c9d8b0 0%,#7aa153 45%,#3f7a2a 100%)}
.hero .caption{position:absolute;left:100px;top:206px;font-size:32px;color:var(--pink);text-shadow:0 0 3px #fff;white-space:nowrap}
.hero svg.arrow{position:absolute;top:146px}
.shade{top:422px;left:60px;width:585px;height:16px;background:radial-gradient(ellipse at top,rgba(0,0,0,.12),transparent 70%)}

.welcome{left:79px;top:446px;width:334px}
.welcome h1{font-size:21px;color:var(--pink-text);line-height:28px}
.welcome .lead{font-size:7.2px;font-weight:600;line-height:11px;margin-top:8px}
.welcome .body{font-size:5.6px;line-height:12.6px;color:var(--grey);margin-top:8px}
.video{left:423px;top:450px;width:204px;height:154px;background:linear-gradient(135deg,#6b4b5e,#3a2d3c 60%,#1c1a22)}

.services-title{top:624px;left:0;width:705px;text-align:center;font-size:21px;color:var(--pink-text);line-height:28px}
.services-sub{top:659px;left:0;width:705px;text-align:center;font-size:5.6px;color:var(--grey)}
.cards{top:681px;left:78px;display:flex;gap:8px}
.card{width:131px;height:179px;background:var(--card);border:1px solid #eee}
.card .photo{height:86px}
.card h3{font-size:7.5px;font-weight:700;margin:10px 6px 6px;text-transform:uppercase}
.card p{font-size:5.5px;line-height:11px;color:var(--grey);margin:0 6px}
.card .btn{display:inline-block;margin:10px 0 0 6px;width:72px;height:20px;background:var(--slate);color:#fff;font-size:6px;line-height:20px;text-align:center;border-radius:2px}
.card.featured{background:var(--slate);box-shadow:0 2px 6px rgba(0,0,0,.3)}
.card.featured h3,.card.featured p{color:#fff}
.card.featured .btn{background:#fff;color:var(--slate)}
.cards-arrow{top:758px}

.band{top:898px;left:0;width:705px;height:95px;background:var(--pink)}
.band p{position:absolute;left:78px;top:34px;width:320px;font-size:6px;line-height:11px;color:#fff}
.band .cta{position:absolute;left:437px;top:32px;width:190px;height:36px;background:#1a0f12;color:#fff;font-size:15px;line-height:36px;text-align:center}

.footer{top:993px;left:0;width:705px;height:172px;background:var(--dark);color:#fff}
.col{position:absolute;top:26px}
.col h4{font-size:14px;line-height:16px;border-left:1px solid #fff;padding-left:12px;margin-left:-1px}
.col ul{list-style:none;margin-top:18px}
.quick li{font-size:5.5px;font-weight:600;line-height:11.2px}
.svc li{font-size:6.5px;line-height:11.2px;color:#ddd}
.news p{font-size:5.5px;font-weight:600;line-height:11px;margin-top:20px;width:155px}
.news form{display:flex;margin-top:12px}
.news input{width:130px;height:20px;border:0;font:6px var(--sans);padding-left:5px}
.news button{width:29px;height:20px;border:0;background:var(--pink);display:flex;align-items:center;justify-content:center}
.photos{display:grid;grid-template-columns:repeat(3,53px);gap:3px;margin-top:18px}
.photos div{height:30px}
.bottom{top:1165px;left:0;width:705px;height:35px;background:var(--darker);color:#fff}
.bottom small{position:absolute;left:81px;top:14px;font-size:5.5px;font-weight:600}
.socials{position:absolute;left:568px;top:12px;display:flex;gap:6px}
.socials span{width:9px;height:9px;background:var(--pink);border-radius:2px}
</style>
</head>
<body>

<div class="contact abs" style="left:78px">
  <div class="ring"><svg width="8" height="10" viewBox="0 0 8 10"><rect x="2" y="0" width="4" height="6" rx="2" fill="#ee4a6a"/><path d="M1 5a3 3 0 0 0 6 0M4 8v2" stroke="#ee4a6a" fill="none"/></svg></div>
  <div><span class="label">Give us a call</span><span class="value">5550142276</span></div>
</div>
<div class="brand abs">
  <div class="mark"></div>
  <div class="name">Tindlewood</div>
  <div class="sub">pet center</div>
</div>
<div class="contact abs" style="left:512px">
  <div class="ring"><svg width="10" height="8" viewBox="0 0 10 8"><rect width="10" height="8" rx="1" fill="#ee4a6a"/><path d="M1 1l4 3 4-3" stroke="#fff" fill="none"/></svg></div>
  <div><span class="label">Email</span><span class="value">hello@tindlewoodpets.com</span></div>
</div>

<nav class="nav abs">
  <a class="active">HOME</a><a>BOARDING</a><a>DAYCARE</a><a>GROOMING</a><a>TRAINING</a><a>BOUTIQUE</a><a>BLOG</a><a>CONTACT</a><a>ABOUT US</a>
</nav>

<section class="hero abs" role="img" aria-label="Beagle puppy running on grass with a red ball">
  <svg class="arrow" style="left:24px" width="22" height="28" viewBox="0 0 22 28"><path d="M18 2L4 14l14 12" stroke="#fff" stroke-width="5" fill="none" opacity=".8"/></svg>
  <svg class="arrow" style="left:660px" width="22" height="28" viewBox="0 0 22 28"><path d="M4 2l14 12L4 26" stroke="#fff" stroke-width="5" fill="none" opacity=".8"/></svg>
  <div class="caption script">Pets only can do full fill the house . . .</div>
</section>
<div class="shade abs"></div>

<section class="welcome abs">
  <h1 class="script">Welcome to Tindlewood pet center</h1>
  <p class="lead">A pet paradise providing the best pet care in the greater Fort Lauderdale FL area. Professional cat &amp; dog boarding, doggy daycare, pet grooming, training, holistic foods &amp; pet boutique.</p>
  <p class="body">Discover how much Tindlewood has to offer for your pet boarding needs by viewing a virtual tour of our 18,000 s/f 'Home Away From Home'. See 9,000 s/f of air conditioned space and a 4,000 s/f outdoor playground with a splash pool. Why not just come by and take a tour of our Fort Lauderdale FL retail store, grooming salon and air conditioned suites? If you prefer to set a time that is best for you, call us on (555) 014.2276. We're always happy to accommodate you Let us pamper your pets with our large air conditioned dog boarding suites, raised platform beds, playtime activities, frolicking in the pool, special meal preparations plus the finest in pet grooming and spa services. Our staff will lovingly care for your special pet from the minute they step into our center until you're ready to pick them up. We think pets are people, too! For immediate pet boarding attention call (555) 014.2276.</p>
</section>
<div class="video abs" role="img" aria-label="Video player showing a tour of the pet store shelves"></div>

<h2 class="services-title abs script">Our services</h2>
<p class="services-sub abs">For prompt and courteous service call us on (555) 014.2276</p>

<svg class="cards-arrow abs" style="left:45px" width="8" height="12" viewBox="0 0 8 12"><path d="M7 1L2 6l5 5" stroke="#4f5a68" fill="none" stroke-width="1.2"/></svg>
<svg class="cards-arrow abs" style="left:652px" width="8" height="12" viewBox="0 0 8 12"><path d="M1 1l5 5-5 5" stroke="#4f5a68" fill="none" stroke-width="1.2"/></svg>
<div class="cards abs">
  <article class="card featured">
    <div class="photo" role="img" aria-label="Staff member sitting with a group of small dogs" style="background:linear-gradient(#b9a594,#8c8378)"></div>
    <h3>Dog Day Car</h3><p>Lorem Ipsum is simply dummy text of the printing and typesetting industry.</p><span class="btn">READ MORE</span>
  </article>
  <article class="card">
    <div class="photo" role="img" aria-label="Small dog resting on a raised boarding bed" style="background:linear-gradient(#e0c9a4,#a9774d)"></div>
    <h3>Dog/Cat Boarding</h3><p>Lorem Ipsum is simply dummy text of the printing and typesetting industry.</p><span class="btn">READ MORE</span>
  </article>
  <article class="card">
    <div class="photo" role="img" aria-label="Groomed dog wearing blue hair rollers" style="background:linear-gradient(#dcdcdc,#9a9a9a)"></div>
    <h3>Dog Grooming</h3><p>Lorem Ipsum is simply dummy text of the printing and typesetting industry.</p><span class="btn">READ MORE</span>
  </article>
  <article class="card">
    <div class="photo" role="img" aria-label="Dogs during a training session indoors" style="background:linear-gradient(#c9b49a,#8a5a38)"></div>
    <h3>Dog Training</h3><p>Lorem Ipsum is simply dummy text of the printing and typesetting industry.</p><span class="btn">READ MORE</span>
  </article>
</div>

<section class="band abs">
  <p>Lorem Ipsum is simply dummy text of the printing and typesetting industry. Lorem Ipsum has been the industry's standard dummy text ever since the 1500s, when an unknown printer took a galley of type and scrambled it to make</p>
  <div class="cta script">Book an Appointment Today!</div>
</section>

<footer class="footer abs">
  <div class="col news" style="left:81px">
    <h4 class="script">News letter</h4>
    <p>Vestibulum ante ipsum primis in faucibus orci luctus et ultrices posuere cubilia Curae; Etiam id enim egestas, congue est id, hendrerit magna.</p>
    <form><input placeholder="Email Address..."><button type="button"><svg width="11" height="11" viewBox="0 0 11 11"><circle cx="5.5" cy="5.5" r="4.6" stroke="#fff" fill="none" stroke-width="1.2"/><path d="M3 5.5h4.5M5.5 3.5l2 2-2 2" stroke="#fff" fill="none" stroke-width="1.2"/></svg></button></form>
  </div>
  <div class="col quick" style="left:270px">
    <h4 class="script">Quick Link</h4>
    <ul><li>Home</li><li>Boarding</li><li>Daycare</li><li>Grooming</li><li>Training</li><li>Boutique</li><li>Blog</li><li>Contact</li><li>About Us</li></ul>
  </div>
  <div class="col svc" style="left:370px">
    <h4 class="script">Services</h4>
    <ul><li>Dog day car</li><li>Dog/cat boarding</li><li>Dog grooming</li><li>Dog training</li><li>Pet food toy</li><li>Clothing</li></ul>
  </div>
  <div class="col" style="left:462px">
    <h4 class="script">Recent Photos</h4>
    <div class="photos">
      <div role="img" aria-label="Dogs at play area" style="background:#6f8a6a"></div>
      <div role="img" aria-label="Dog in boarding suite" style="background:#8a7a6a"></div>
      <div role="img" aria-label="Dog on floor" style="background:#b7b0a4"></div>
      <div role="img" aria-label="Dogs by a gate" style="background:#5a5a5a"></div>
      <div role="img" aria-label="Dog resting indoors" style="background:#9a7a5a"></div>
      <div role="img" aria-label="Pet treats on display" style="background:#c08a6a"></div>
    </div>
  </div>
</footer>
<div class="bottom abs">
  <small>Copyright © 2015 tindlewoodpetcenter All rights reserved.</small>
  <div class="socials"><span></span><span></span><span></span><span></span></div>
</div>

</body>
</html>
```